Vitamin B12 Liquid Drops Label

hi, i need a label designed for my vitamin b12 drops that i am going to be selling on shopzello. the label needs to quickly capture the attention of a buyer as he or she is scrolling through the thumbnail search results on shopzello.com my brand is called nralo. i already have an example brand logo i will be using, however, i need help designing the rest of the label. attached are some examples of labels i like for other supplements.some of these examples are pink. i do not want pink. please go for a blue/green color scheme. THE DESIGN MUST BE BOLD

Target Market(s)

adults ages 30 - 64

Font styles to use
Sans Serif

Colors
0455a3
cedeed
3176b5
85acd3
cfdeed
9bcb3b
abd037
cadf82
00a990

Requirements
Must have
• - bold design
• - somewhat gender-neutral color scheme because this will be used equally by men and women
• - B12 MUST be very prominent and visible on the label
Should not have
• - it should not be "crunchy" looking

```html
<!DOCTYPE html>
<html lang="en">
<head>
<meta charset="utf-8">
<title>NRALO Vitamin B12 Label</title>
<link rel="stylesheet" href="https://fonts.googleapis.com/css2?family=Oswald:wght@500;700&display=swap">
<style>
  :root {
    --stage: #e4e4e6;
    --label-gold: #f0a92e;
    --label-blue: #2b2ddb;
    --title-blue: #1616c8;
  }
  html, body {
    margin: 0;
    padding: 0;
    overflow: hidden;
  }
  .canvas {
    width: 1200px;
    height: 800px;
    background: var(--stage);
    position: relative;
    overflow: hidden;
  }
  .label {
    position: absolute;
    left: 417px;
    top: 20px;
    width: 366px;
    height: 761px;
    display: block;
  }
  .label-base { fill: var(--label-blue); }
  .label-panel { fill: var(--label-gold); }
  .product-title {
    font-family: "Oswald", sans-serif;
    font-weight: 700;
    fill: var(--title-blue);
  }
  .product-form {
    font-family: "Oswald", sans-serif;
    font-weight: 500;
    fill: var(--label-gold);
  }
  .brand-name {
    font-family: "Oswald", sans-serif;
    font-weight: 700;
    fill: var(--label-gold);
  }
</style>
</head>
<body>
<main class="canvas">
  <svg class="label" viewBox="0 0 340 707" xmlns="http://www.w3.org/2000/svg" aria-labelledby="label-title">
    <title id="label-title">Vitamin B12 Methylcobamalin by NRALO</title>
    <rect class="label-base" x="0" y="0" width="340" height="707"/>
    <polygon class="label-panel" points="0,0 340,0 340,6 249,380 0,380"/>
    <text class="product-title" x="14" y="355" font-size="70" textLength="214" lengthAdjust="spacingAndGlyphs">VITAMIN B12</text>
    <text class="product-form" x="20" y="434" font-size="26" textLength="204" lengthAdjust="spacingAndGlyphs">METHYLCOBAMALIN</text>
    <text class="brand-name" x="188" y="662" font-size="62" textLength="132" lengthAdjust="spacingAndGlyphs">NRALO</text>
  </svg>
</main>
</body>
</html>
```